New Bicycle shop business card

Hi!
I'm looking for a business card for my new proffesional bike mechanics shop. This shop is only for fixing broken bikes and not selling bikes.
Peferbly a modern and sleek and modern design.
Colors: black, grey, red, white
Information:
Name: Rijwielwerkplaats Vanhoutte
Shop owner: Bart Vanhoutte & Marieke Segers
Website: www.rijwielwerkplaats-vanhoutte.be
Email: info@rijwielwerkplaats-vanhoutte.be
Phone number: +32471902368
Street adres: Kerkweg 46
9940 Bellebeke
Slogan/shop information: Herstellingen van alle merken.
Logo: see files.
Target Market(s)
People who seek a mechanic to fix or upgrade their bikes.
Contact Information for Business Card
Information:
Website: info@rijwielwerkplaats-vanhoutte.be
9940 Bellebeke
Logo: see files.

```html
<!DOCTYPE html>
<html lang="nl">
<head>
<meta charset="utf-8">
<title>Rijwielwerkplaats Vanhoutte – visitekaartje</title>
<link rel="stylesheet" href="https://fonts.googleapis.com/css2?family=Didact+Gothic&family=Montserrat:wght@800&display=swap">
<style>
  :root {
    --canvas: #d9d4cc;
    --card: #f1f2f1;
    --card-edge: #f8f9f8;
    --ink: #232323;
    --red: #c3161f;
    --white: #ffffff;
  }
  * { margin: 0; padding: 0; box-sizing: border-box; }
  html, body { width: 1200px; height: 970px; overflow: hidden; }
  body {
    background: var(--canvas);
    display: flex;
    align-items: center;
    justify-content: center;
    font-family: "Didact Gothic", "Century Gothic", sans-serif;
    color: var(--ink);
  }
  .card {
    position: relative;
    width: 1000px;
    height: 570px;
    background: linear-gradient(135deg, var(--card-edge), var(--card));
    box-shadow: 0 14px 40px rgba(0,0,0,.18);
  }
  .brand {
    position: absolute;
    left: 80px;
    top: 110px;
    font-family: "Montserrat", sans-serif;
    font-weight: 800;
    color: var(--ink);
    line-height: 1.05;
  }
  .brand-name { font-size: 34px; letter-spacing: 1px; }
  .brand-sub { font-size: 30px; letter-spacing: 12px; }
  .slogan {
    position: absolute;
    left: 80px;
    top: 200px;
    font-size: 19px;
    letter-spacing: 3px;
  }
  .owners {
    position: absolute;
    left: 80px;
    top: 262px;
    font-size: 26px;
    text-transform: uppercase;
    letter-spacing: .3px;
  }
  .contact {
    position: absolute;
    left: 80px;
    top: 348px;
    list-style: none;
  }
  .contact li {
    display: flex;
    align-items: center;
    height: 36px;
    font-size: 23px;
  }
  .contact svg { width: 28px; height: 28px; margin-right: 18px; flex: none; }
  .mark {
    position: absolute;
    left: 620px;
    top: 110px;
    width: 340px;
    height: 340px;
    border-radius: 50%;
    background: var(--red);
  }
</style>
</head>
<body>
  <div class="card">
    <div class="brand">
      <div class="brand-name">RIJWIELWERKPLAATS</div>
      <div class="brand-sub">VANHOUTTE</div>
    </div>
    <p class="slogan">Herstellingen van alle merken</p>
    <p class="owners">Bart Vanhoutte &amp; Marieke Segers</p>
    <ul class="contact">
      <li>
        <svg viewBox="0 0 28 28" aria-hidden="true"><circle cx="14" cy="14" r="14" fill="var(--red)"/><path d="M9.5 7.5l3 3-1.8 1.8c.9 2 2.6 3.7 4.6 4.6l1.8-1.8 3 3-1.9 1.9c-5.5-.6-10-5.1-10.6-10.6z" fill="var(--white)"/></svg>
        +32471902368
      </li>
      <li>
        <svg viewBox="0 0 28 28" aria-hidden="true"><circle cx="14" cy="14" r="14" fill="var(--red)"/><rect x="7.5" y="9.5" width="13" height="9" fill="none" stroke="var(--white)" stroke-width="1.6"/><path d="M7.5 9.5l6.5 5 6.5-5" fill="none" stroke="var(--white)" stroke-width="1.6"/></svg>
        info@rijwielwerkplaats-vanhoutte.be
      </li>
      <li>
        <svg viewBox="0 0 28 28" aria-hidden="true"><circle cx="14" cy="14" r="14" fill="var(--red)"/><g fill="none" stroke="var(--white)" stroke-width="1.4"><circle cx="14" cy="14" r="7"/><ellipse cx="14" cy="14" rx="3" ry="7"/><path d="M7 14h14"/></g></svg>
        www.rijwielwerkplaats-vanhoutte.be
      </li>
      <li>
        <svg viewBox="0 0 28 28" aria-hidden="true"><circle cx="14" cy="14" r="14" fill="var(--red)"/><path d="M14 6.5a5 5 0 0 1 5 5c0 3.8-5 9.5-5 9.5s-5-5.7-5-9.5a5 5 0 0 1 5-5z" fill="var(--white)"/><circle cx="14" cy="11.5" r="1.9" fill="var(--red)"/></svg>
        Kerkweg 46, 9940 Bellebeke
      </li>
    </ul>
    <div class="mark" aria-hidden="true"></div>
  </div>
</body>
</html>
```